Vantoq Business Card Project showing the logo and a marbo image on the rear

Design a whacky but professional business card, the logo is for the front and the Marbo image is for the rear. Happy to consider other open source Marbo Images if the designer wants to select one from the web. Vantoq is a competitor to OMB.com.au and Pellory.com.au and is based around every property in Australia

Target Market(s)

Business

Contact Information for Business Card

Name, Title, Email, Web, Phone Number

Font styles to use
Other font styles liked:
• avenir

Requirements
Must have
• Image on Back logo on front
Nice to have
• Happy to consider other images on rear, preftably Colin Marbo. Image supplied I own, we can use open source other Marbo Images

```html
<!DOCTYPE html>
<html lang="en">
<head>
<meta charset="utf-8">
<title>Vantoq Business Card</title>
<link rel="stylesheet" href="https://fonts.googleapis.com/css2?family=Nunito+Sans:wght@700;800&family=Roboto:wght@400&display=swap">
<style>
  :root {
    --backdrop: #2b2b2b;
    --orange: #ec8304;
    --charcoal: #3d3f42;
    --paper: #f2f2f2;
    --ink: #1d1d1b;
  }
  * { margin: 0; padding: 0; box-sizing: border-box; }
  html, body { width: 1138px; height: 1200px; overflow: hidden; }
  body { background: var(--backdrop); position: relative; font-family: "Roboto", Arial, sans-serif; }

  .card {
    position: absolute;
    top: 275px;
    width: 375px;
    height: 620px;
    border-radius: 12px;
    overflow: hidden;
  }
  .card-back { left: 156px; }
  .card-front { left: 577px; background: var(--paper); }

  .artwork { position: absolute; inset: 0; }
  .artwork .sky-day { position: absolute; left: 0; top: 0; width: 50%; height: 100%; background: var(--orange); }
  .artwork .sky-night { position: absolute; right: 0; top: 0; width: 50%; height: 100%; background: var(--charcoal); }
  .artwork .city {
    position: absolute; left: 0; right: 0; bottom: 0; height: 48%;
    background: linear-gradient(180deg, #d9448e 0%, #c8d640 40%, #f2e04a 70%, #6cc4d8 88%, #7cc23c 100%);
  }

  .front-shape { position: absolute; inset: 0; }

  .brand {
    position: absolute; left: 0; right: 0; top: 50px;
    display: flex; flex-direction: column; align-items: center; gap: 18px;
  }
  .brand-mark { width: 92px; height: 92px; background: var(--orange); border-radius: 4px; }
  .brand-name { font-family: "Nunito Sans", Arial, sans-serif; font-weight: 800; font-size: 38px; color: var(--ink); line-height: 1; }

  .person { position: absolute; left: 0; right: 0; top: 322px; text-align: center; color: var(--ink); }
  .person-name { font-family: "Nunito Sans", Arial, sans-serif; font-weight: 700; font-size: 25px; line-height: 1.2; }
  .person-title { font-size: 16px; margin-top: 6px; }

  .divider { position: absolute; left: 59px; right: 59px; top: 410px; height: 28px; display: flex; align-items: center; justify-content: space-between; }
  .divider-line { width: 72px; height: 2px; background: var(--ink); }
  .contact-icons { display: flex; gap: 5px; }
  .contact-icons svg { width: 27px; height: 27px; display: block; }

  .contact { position: absolute; left: 0; right: 0; top: 448px; text-align: center; color: var(--ink); font-size: 16px; line-height: 24px; }
  .address { position: absolute; left: 0; right: 0; top: 538px; text-align: center; color: var(--ink); font-size: 16px; line-height: 24px; }
</style>
</head>
<body>
  <section class="card card-back">
    <div class="artwork" role="img" aria-label="Colourful pop-art city illustration: sunny orange sky on one half, starry night sky with a plane on the other, cheerful buildings and a train along the bottom">
      <div class="sky-day"></div>
      <div class="sky-night"></div>
      <div class="city"></div>
    </div>
  </section>

  <section class="card card-front">
    <svg class="front-shape" viewBox="0 0 375 620" preserveAspectRatio="none" aria-hidden="true">
      <path d="M150 278 Q280 290 375 222 L375 236 Q280 302 150 282 Z" fill="#1d1d1b"/>
      <path d="M0 218 Q190 338 375 232 L375 620 L0 620 Z" fill="var(--orange)"/>
    </svg>

    <div class="brand">
      <div class="brand-mark"></div>
      <div class="brand-name">Vantoq</div>
    </div>

    <div class="person">
      <div class="person-name">Neil Farrow</div>
      <div class="person-title">Founder &amp; CEO</div>
    </div>

    <div class="divider">
      <span class="divider-line"></span>
      <span class="contact-icons">
        <svg viewBox="0 0 28 28" aria-label="Phone"><circle cx="14" cy="14" r="12.5" fill="none" stroke="#1d1d1b" stroke-width="2"/><path d="M8 12 Q14 6 20 12 L18 14 L16 12 L12 12 L10 14 Z M10 15 H18 V20 H10 Z" fill="#1d1d1b"/></svg>
        <svg viewBox="0 0 28 28" aria-label="Email"><circle cx="14" cy="14" r="12.5" fill="none" stroke="#1d1d1b" stroke-width="2"/><rect x="7.5" y="9.5" width="13" height="9" fill="#1d1d1b"/><path d="M8 10 L14 15 L20 10" fill="none" stroke="var(--orange)" stroke-width="1.4"/></svg>
        <svg viewBox="0 0 28 28" aria-label="Website"><circle cx="14" cy="14" r="12.5" fill="none" stroke="#1d1d1b" stroke-width="2"/><circle cx="14" cy="14" r="6.5" fill="none" stroke="#1d1d1b" stroke-width="1.4"/><ellipse cx="14" cy="14" rx="2.8" ry="6.5" fill="none" stroke="#1d1d1b" stroke-width="1.2"/><path d="M7.5 14 H20.5" stroke="#1d1d1b" stroke-width="1.2"/></svg>
      </span>
      <span class="divider-line"></span>
    </div>

    <div class="contact">
      <div>(00) 4816 2739</div>
      <div>farrow@vantoq.com</div>
      <div>www.vantoq.com</div>
    </div>

    <div class="address">
      <div>Level 4, 18 Calder Lane,</div>
      <div>Sydney 2000, Australia</div>
    </div>
  </section>
</body>
</html>
```